Start-Up für Training, Coaching & Consulting sucht modernes Webdesign!
Zielgruppe
Wer ist TAVI Training, Coaching & Consulting?
Wir führen Führungskräftetrainings durch, machen Privatkunden für Bewerbungen fit und unterstützen Unternehmen mit Verkaufstrainings. Wir entwickeln Persönlichkeiten im Coaching. Wir beraten Unternehmen und helfen ihnen dabei, ihre Geschäftsabläufe und Prozesse zu optimieren. Dabei steht unsere hohe Qualität im Mittelpunkt - gemeinsam mit unseren kreativen Trainingsmethoden. Unser Background (Diplom-Kaufleute und geprüfte Trainer) bietet dafür die passende Ausgangslage.
Was bedeutet TAVI?
Tavi ist Maori und bdeutet Kreis/Spirale. Er symbolisiert einen wachsenden Silberfarn und steht für persönliche Entwicklung und Entfaltung. Der Tavi ist einerseits unser Namensgeber und unser Logo, andererseits steht der Tavi aber auch für unsere Werte: Denn wir wollen unseren Kunden dabei helfen zu wachsen und sich weiterzuentwickeln - und dies auf eine hochqualitative und seriöse Art und Weise ohne den Eindruck von Esoterik oder Erlebnispädagogik zu vermitteln.
Aufgabenstellung
Modernes Design, das unsere Philosophie widerspiegelt: Wir möchten unseren Kunden auf seriöse und hochqualitative Weise weiterentwickeln. Wir stehen für nachhaltigen Lernerfolg, kreative Trainingsmethoden, Abwechslung, Spaß am Lernen, Qualität, Kompetenz, Fachwissen und Dynamik.
Layout:
1) Header: QMSR geprüfter Trainer, Menüpunkte (siehe Architektur)
2) Banner
3) 3 Teaser (Training, Coaching, Consulting) + Header + 2-3 Zeilen Text (+Icons)
>>> Sichtbarer Bereich auf Homepage: Menü, Banner, Teaser
4) "Warum Sie uns wählen sollten": 5 bullet points ohne weiteren Text
5) "Aus unserem Blog": Frame für 3 Blogartikel + Bild + Datum + Header + 2-3 Zeilen Text
6) Alle drei QMSR Logos
7) Footer: Click Us (quick links), Contact Us (Adresse), Follow Us (Pinnwald, ZOLP, Kontaktor)
8) Copyright + Impressum
>>> Das Design soll klar sein, aber nicht zu kantig. Vielmehr sollen abgerundete Ecken und dynamische Elemente genutzt werden.
Architektur:
3 Ebenen:
1) Homepage
2) TAVI, Training, Coaching, Consulting, für Trainer, Kundenstimmen/Referenzen, Kontakt
3) noch zu bestimmende Produktdetailseiten
Texte werden noch erstellt, Layout kann ggf. mit Platzhaltertext gefüllt werden.
Bildmaterial: Logo und vorhandenes Imagebild werden zur Verfügung gestellt. Bilder können ggf. gekauft werden. Vorschläge erwünscht.
Corporate colors:
grün: #a2c61b + monochromatic colors
http://www.tintoskop.de/a2c61b
grau: #474747 + monochromatic colors
http://www.tintoskop.de/474747

```html
<!DOCTYPE html>
<html lang="en">
<head>
<meta charset="utf-8">
<title>TAVI – Training · Coaching · Consulting</title>
<link href="https://fonts.googleapis.com/css2?family=Lato:ital,wght@0,300;0,400;0,700;1,300&display=swap" rel="stylesheet">
<style>
:root{
  --green:#a2c61b;
  --green-dark:#86a614;
  --grey:#474747;
  --grey-dark:#333333;
  --grey-text:#8a8a8a;
  --card-bg:#f5f5f5;
  --white:#ffffff;
}
*{margin:0;padding:0;box-sizing:border-box}
html,body{width:1120px;height:1200px;overflow:hidden}
body{font-family:"Lato",sans-serif;font-weight:300;color:var(--grey);background:var(--white);position:relative}
.abs{position:absolute}

/* top bar */
.topbar{left:0;top:0;width:1120px;height:17px;background:var(--grey);color:#ddd;font-size:8.5px}
.topbar .contact{position:absolute;left:227px;top:4px;display:flex;align-items:center;gap:6px}
.topbar svg{width:7px;height:7px;fill:var(--green)}
.topbar .sep{width:1px;height:9px;background:#777}
.topbar .lang{position:absolute;left:856px;top:4px}

/* header */
.header{left:0;top:17px;width:1120px;height:58px;background:#fafafa}
.brand{position:absolute;left:227px;top:9px}
.brand .name{font-size:27px;font-weight:700;color:var(--grey);letter-spacing:1px;line-height:1}
.brand .tag{font-size:5.5px;color:var(--grey);font-weight:400;margin-top:4px}
.trainer-badge{position:absolute;left:809px;top:7px;width:83px;height:23px;background:#1f5fa8;border-radius:2px}
.nav{position:absolute;left:426px;top:39px;display:flex;font-size:9.2px;font-weight:400;text-transform:uppercase}
.nav a{color:var(--grey);text-decoration:none;padding:0 10px 10px 10px;margin-right:5px;position:relative}
.nav a.active{color:var(--green)}
.nav a.active::after{content:"";position:absolute;left:0;right:0;bottom:0;height:2px;background:var(--green)}

/* hero */
.hero{left:0;top:75px;width:1120px;height:222px;background:radial-gradient(ellipse at 55% 35%,#6f9a3b 0%,#3d6a22 35%,#1d3a12 80%)}
.hero h1{position:absolute;left:236px;top:62px;font-size:22px;font-weight:400;color:var(--green)}
.hero p{position:absolute;left:238px;top:94px;width:300px;font-size:10px;line-height:13px;color:var(--white);font-weight:400}
.btn-solid{position:absolute;left:238px;top:131px;width:137px;height:26px;background:var(--green);color:var(--white);font-size:11px;font-weight:400;display:flex;align-items:center;justify-content:center}

/* teaser cards */
.card{top:333px;width:216px;height:296px;border:3px solid var(--green);border-radius:10px;background:var(--card-bg);overflow:hidden;text-align:center}
.card .photo{height:142px;background:linear-gradient(135deg,#c9d3db,#8ea0ad 55%,#4c5660);border-bottom:2px solid var(--green)}
.card .icon{position:absolute;left:82px;top:116px;width:52px;height:52px;border-radius:50%;background:var(--green);border:2px solid var(--white)}
.card h2{margin-top:38px;font-size:13.5px;font-weight:400;color:var(--grey)}
.card p{margin:8px auto 0;width:176px;font-size:8.5px;line-height:13px;color:var(--grey-text)}
.btn-outline{display:inline-flex;align-items:center;justify-content:center;margin-top:10px;width:87px;height:20px;border:1px solid var(--green);border-radius:4px;color:var(--green);font-size:10px;font-weight:400;background:var(--white)}

/* green section */
.why{left:0;top:665px;width:1120px;height:269px;background:var(--green);color:var(--white)}
.why h3{position:absolute;font-size:14.5px;font-weight:400;text-transform:uppercase}
.checklist{position:absolute;left:236px;top:66px;list-style:none}
.checklist li{position:relative;padding-left:26px;height:34.5px;font-size:9px;line-height:13px;width:310px;font-weight:400}
.checklist svg{position:absolute;left:2px;top:4px;width:11px;height:11px}
.divider{position:absolute;left:560px;top:80px;width:1px;height:150px;background:rgba(255,255,255,.35)}
.post{position:absolute;left:580px;width:310px;height:47px}
.post .thumb{position:absolute;left:0;top:0;width:93px;height:47px;border-radius:2px;background:radial-gradient(circle at 50% 60%,#8fbf52,#3f6d25 70%,#23401a)}
.post h4{position:absolute;left:103px;top:2px;font-size:11.5px;font-weight:400}
.post .date{position:absolute;left:103px;top:19px;font-size:8.5px;font-style:italic}
.post .excerpt{position:absolute;left:103px;top:34px;font-size:8.5px;font-weight:400;white-space:nowrap}
.post .excerpt span{color:#e6f0bd}

/* partner badges */
.partners{left:0;top:934px;width:1120px;height:80px;background:var(--white)}
.partners .badge{position:absolute;background:#c7c7c7;border-radius:2px}

/* footer */
.footer{left:0;top:1014px;width:1120px;height:186px;background:var(--grey-dark);color:#d6d6d6}
.footer h5{position:absolute;top:27px;font-size:10.5px;font-weight:400;color:var(--white);text-transform:uppercase}
.quick{position:absolute;left:291px;top:53px;list-style:none;font-size:9px}
.quick li{height:18px;display:flex;align-items:center;gap:6px}
.quick li::before{content:"";border-left:4px solid #bbb;border-top:2.5px solid transparent;border-bottom:2.5px solid transparent}
.quick li.current{color:var(--green)}
.quick li.current::before{border-left-color:var(--green)}
.address{position:absolute;left:509px;font-size:9px;line-height:13px;display:flex;gap:7px}
.address svg{width:7px;height:8px;fill:#aaa;margin-top:3px;flex:none}
.social{position:absolute;left:752px;top:58px;display:flex;gap:10px;font-size:10px;font-weight:700;color:var(--white)}
.foot-brand{position:absolute;left:752px;top:85px;color:#9a9a9a}
.foot-brand .name{font-size:24px;font-weight:700;letter-spacing:1px;line-height:1}
.foot-brand .tag{font-size:5px;margin-top:4px}
.foot-rule{position:absolute;left:227px;top:163px;width:665px;height:1px;background:#5a5a5a}
.foot-meta{position:absolute;top:169px;font-size:8px;color:#bbb}
</style>
</head>
<body>

<div class="abs topbar">
  <div class="contact">
    <svg viewBox="0 0 10 10"><path d="M2 0l2 2-1 1.5c.6 1.4 1.8 2.6 3.2 3.2L7.7 5.7 10 7.7 8.5 10C4 9.6.4 6 0 1.5z"/></svg>
    <span>12 0000 111</span><span class="sep"></span>
    <svg viewBox="0 0 10 8"><path d="M0 0h10v1L5 4 0 1zM0 2l5 3 5-3v6H0z"/></svg>
    <span>hello@tavi.one</span>
  </div>
  <div class="lang">English &nbsp;▾</div>
</div>

<header class="abs header">
  <div class="brand"><div class="name">TAVI</div><div class="tag">Training • Coaching • Consulting</div></div>
  <div class="trainer-badge" role="img" aria-label="Certified trainer badge"></div>
  <nav class="nav">
    <a class="active">Home</a><a>About us</a><a>Training</a><a>Coaching</a><a>Consultant</a><a>Jobs</a><a>Contact us</a>
  </nav>
</header>

<section class="abs hero" role="img" aria-label="Close-up of an unfurling green fern frond">
  <h1>WELCOME TEXT</h1>
  <p>Lorem Ipsum is simply dummy text of the printing and typesetting industry. Lorem Ipsum has been the industry's standard.</p>
  <div class="btn-solid">CONTACT US</div>
</section>

<article class="abs card" style="left:227px">
  <div class="photo" role="img" aria-label="Trainer presenting at a flipchart to a seated group"></div>
  <div class="icon" role="img" aria-label="Training icon"></div>
  <h2>TRAINING</h2>
  <p>Lorem Ipsum is simply dummy text of the printing and typesetting industry. Lorem Ipsum has been the industry's standard</p>
  <span class="btn-outline">Read More</span>
</article>
<article class="abs card" style="left:452px">
  <div class="photo" role="img" aria-label="Coaching conversation between colleagues at a table"></div>
  <div class="icon" role="img" aria-label="Coaching icon"></div>
  <h2>COACHING</h2>
  <p>Lorem Ipsum is simply dummy text of the printing and typesetting industry. Lorem Ipsum has been the industry's standard</p>
  <span class="btn-outline">Read More</span>
</article>
<article class="abs card" style="left:676px">
  <div class="photo" role="img" aria-label="Consultant in a suit beside an empty meeting room"></div>
  <div class="icon" role="img" aria-label="Consulting icon"></div>
  <h2>CONSULTING</h2>
  <p>Lorem Ipsum is simply dummy text of the printing and typesetting industry. Lorem Ipsum has been the industry's standard</p>
  <span class="btn-outline">Read More</span>
</article>

<section class="abs why">
  <h3 style="left:236px;top:40px">Why choose us</h3>
  <ul class="checklist">
    <li><svg viewBox="0 0 12 12"><path d="M1 7l3 4 7-10" fill="none" stroke="#fff" stroke-width="1.3"/></svg>Lorem Ipsum is simply dummy text of the printing and typesetting industry. Lorem Ipsum has been the industry's standard dummy text</li>
    <li><svg viewBox="0 0 12 12"><path d="M1 7l3 4 7-10" fill="none" stroke="#fff" stroke-width="1.3"/></svg>Lorem Ipsum is simply dummy text of the printing and typesetting industry. Lorem Ipsum has been the industry's standard dummy text</li>
    <li><svg viewBox="0 0 12 12"><path d="M1 7l3 4 7-10" fill="none" stroke="#fff" stroke-width="1.3"/></svg>Lorem Ipsum is simply dummy text of the printing and typesetting industry. Lorem Ipsum has been the industry's standard dummy text</li>
    <li><svg viewBox="0 0 12 12"><path d="M1 7l3 4 7-10" fill="none" stroke="#fff" stroke-width="1.3"/></svg>Lorem Ipsum is simply dummy text of the printing and typesetting industry. Lorem Ipsum has been the industry's standard dummy text</li>
    <li><svg viewBox="0 0 12 12"><path d="M1 7l3 4 7-10" fill="none" stroke="#fff" stroke-width="1.3"/></svg>Lorem Ipsum is simply dummy text of the printing and typesetting industry. Lorem Ipsum has been the industry's standard dummy text</li>
  </ul>
  <div class="divider"></div>
  <h3 style="left:578px;top:40px">Aus unserem Blog</h3>
  <div class="post" style="top:69px">
    <div class="thumb" role="img" aria-label="Fern frond blog thumbnail"></div>
    <h4>LOREM IPSUM</h4><div class="date">17 December 2015 by Admin</div>
    <div class="excerpt">Lorem Ipsum is simply dummy text of ... <span>read more</span></div>
  </div>
  <div class="post" style="top:128px">
    <div class="thumb" role="img" aria-label="Fern frond blog thumbnail"></div>
    <h4>LOREM IPSUM</h4><div class="date">15 December 2015 by Admin</div>
    <div class="excerpt">Lorem Ipsum is simply dummy text of ... <span>read more</span></div>
  </div>
  <div class="post" style="top:187px">
    <div class="thumb" role="img" aria-label="Fern frond blog thumbnail"></div>
    <h4>LOREM IPSUM</h4><div class="date">9 December 2015 by Admin</div>
    <div class="excerpt">Lorem Ipsum is simply dummy text of ... <span>read more</span></div>
  </div>
</section>

<section class="abs partners">
  <div class="badge" role="img" aria-label="Association member badge" style="left:365px;top:23px;width:52px;height:30px;background:#1f5fa8"></div>
  <div class="badge" role="img" aria-label="Certified trainer badge" style="left:501px;top:25px;width:109px;height:29px"></div>
  <div class="badge" role="img" aria-label="Professional association badge" style="left:686px;top:23px;width:69px;height:30px"></div>
</section>

<footer class="abs footer">
  <h5 style="left:291px">Click us</h5>
  <ul class="quick">
    <li class="current">Lorem Ipsum</li><li>Lorem Ipsum</li><li>Lorem Ipsum</li><li>Lorem Ipsum</li><li>Lorem Ipsum</li>
  </ul>

  <h5 style="left:509px">Contact us</h5>
  <div class="address" style="top:53px"><svg viewBox="0 0 8 10"><path d="M4 0a4 4 0 014 4c0 3-4 6-4 6S0 7 0 4a4 4 0 014-4zm0 2.5a1.5 1.5 0 100 3 1.5 1.5 0 000-3z"/></svg><span>Lindenweg 14<br>D-60000 Musterstadt</span></div>
  <div class="address" style="top:87px"><svg viewBox="0 0 10 8"><path d="M0 0h10v1L5 4 0 1zM0 2l5 3 5-3v6H0z"/></svg><span>hello@tavi.one</span></div>
  <div class="address" style="top:109px"><svg viewBox="0 0 10 10"><path d="M2 0l2 2-1 1.5c.6 1.4 1.8 2.6 3.2 3.2L7.7 5.7 10 7.7 8.5 10C4 9.6.4 6 0 1.5z"/></svg><span>+49 1500 0000 111</span></div>

  <h5 style="left:752px">Follow us</h5>
  <div class="social"><span>Pinnwald</span><span>Kontaktor</span><span>ZOLP</span></div>
  <div class="foot-brand"><div class="name">TAVI</div><div class="tag">Training · Coaching · Consulting</div></div>

  <div class="foot-rule"></div>
  <div class="foot-meta" style="left:236px">Impressum</div>
  <div class="foot-meta" style="left:785px">Copyright © 2015 tavi.one</div>
</footer>

</body>
</html>
```